ourTradeLoop Webdesign - trading your electronics for cash - helping you clear up clutter

We need web design (and an updated logo) for a new company based in London called "ourTradeLoop". It is a platform that enables users to sell their old electronics for cash, either for themselves or they can donate the cash to charity. In time, we also plan to enable buying of electronics on the site. We specialise in mobile phones, tablets, laptops, and games consoles. Please review brindlo.com, which is a US site with the same business, and also tunefernwick.co.uk, so have a similar business in the UK. We would like to see designs that use the colour red, and that are bold. We currently have a logo, and a WIP site built, but the design needs to be dramatically improved, the right colour mix needs to be chosen to give a clean and modern feel. Please review www.ourtradeloop.com to get an understanding of the work that needs to be improved.

Target Market(s)

People who buy electronics frequently, i.e. upgrade every time a new quince product comes out! These guys usually have a lap top, desk top, tablet and phone.

Industry/Entity Type

Electronics

Logo Text

ourTradeLoop

Number of Pages Required

3 page

Font styles to use
Sans Serif

Colors
ec1f27

Requirements
Must have
• Home page design
• "How-it-works" page design
• Sell page design
• Must use the colour red, and have a secondary/accent colour.

```html
<!DOCTYPE html>
<html lang="en">
<head>
<meta charset="utf-8">
<title>ourTradeLoop – Sell Your Electronics</title>
<link href="https://fonts.googleapis.com/css2?family=Raleway:wght@500;600;700;800&family=Open+Sans:wght@400;600;700&display=swap" rel="stylesheet">
<style>
:root{
  --red:#ec1f27;
  --red-soft:#f0555a;
  --ink:#333333;
  --text:#666666;
  --slate:#3f3d5e;
  --panel:#f3f3f3;
  --hero-grey:#e9e9ea;
  --green:#8dc63f;
  --yellow:#e5c02f;
  --blue:#3fa9d6;
  --orange:#f7822c;
  --white:#ffffff;
}
*{margin:0;padding:0;box-sizing:border-box}
html,body{width:1200px;height:2359px;overflow:hidden;background:var(--white)}
body{position:relative;font-family:'Open Sans',sans-serif;color:var(--text)}
.abs{position:absolute}
.heading{font-family:'Raleway',sans-serif;font-weight:700;color:var(--ink);font-size:25px;text-align:center;left:0;width:1200px;letter-spacing:.2px}
.lead{font-size:12px;line-height:24px;text-align:center;left:240px;width:720px}

/* header */
.top-bar{left:0;top:0;width:1200px;height:5px;background:var(--red)}
.brand{display:flex;align-items:center;gap:10px;font-family:'Raleway',sans-serif;font-weight:700;font-size:26px;color:var(--ink);white-space:nowrap}
.brand-mark{width:22px;height:22px;background:var(--red)}
.site-brand{left:99px;top:50px}
.nav-link{top:40px;font-family:'Raleway',sans-serif;font-weight:600;font-size:16px;color:var(--ink)}
.nav-btn{top:33px;width:73px;height:34px;border:2px solid;font-family:'Raleway',sans-serif;font-weight:700;font-size:16px;display:flex;align-items:center;justify-content:center}
.nav-btn.buy{left:942px;color:var(--red);border-color:var(--red)}
.nav-btn.sell{left:1027px;color:var(--slate);border-color:var(--slate)}

/* hero */
.hero{left:0;top:102px;width:1200px;height:480px}
.hero-label{background:rgba(30,30,35,.85);color:var(--white);padding:14px 20px 0 18px;white-space:nowrap}
.hero-label b{display:block;font-family:'Raleway',sans-serif;font-weight:800;font-size:78px;line-height:72px}
.hero-label span{display:block;font-family:'Raleway',sans-serif;font-weight:500;font-size:23px;line-height:30px}

/* gadgets */
.gadget{top:759px;width:126px;height:126px;border-radius:50%;border:4px solid var(--white);box-shadow:0 0 0 2px #e5e5e5;display:flex;align-items:center;justify-content:center}
.arrow{top:804px}

/* app */
.app-band{left:0;top:939px;width:1200px;height:382px;background:linear-gradient(90deg,#4d4b6e 0%,#45435f 55%,#5a5874 100%)}
.app-title{left:167px;top:1024px;font-family:'Raleway',sans-serif;font-weight:700;font-size:25px;color:var(--white)}
.app-copy{left:168px;top:1068px;width:505px;font-size:12px;line-height:25px;color:#e6e6ee}
.store-badge{top:1188px;width:149px;height:42px;background:#111;border:1px solid #777;border-radius:6px}
.hand-photo{left:700px;top:959px;width:300px;height:362px;background:linear-gradient(160deg,#f3f3f3 0%,#d8c2b0 45%,#b98e72 100%);border-radius:40px 40px 0 0}

/* how */
.cta{left:473px;top:1494px;width:254px;height:46px;background:var(--red);color:var(--white);font-weight:700;font-size:14px;display:flex;align-items:center;justify-content:center}

/* why */
.why{left:0;top:1604px;width:1200px;height:374px;background:var(--panel)}
.feature{top:1726px;width:290px;text-align:center}
.feature svg{display:block;margin:0 auto 22px}
.feature h3{font-family:'Raleway',sans-serif;font-weight:700;font-size:15px;color:var(--ink);margin-bottom:12px;white-space:nowrap}
.feature p{font-size:12px;line-height:24px}

/* newsletter */
.newsletter{left:0;top:1978px;width:1200px;height:85px;background:var(--red)}
.nl-label{left:164px;top:1994px;color:var(--white);font-family:'Raleway',sans-serif;font-weight:700}
.nl-label small{display:block;font-size:13px}
.nl-label strong{display:block;font-size:21px}
.nl-input{left:348px;top:1999px;width:621px;height:39px;background:var(--white);font-size:11px;color:#999;padding:12px 16px}
.nl-btn{left:988px;top:1997px;width:114px;height:42px;border:2px solid var(--white);color:var(--white);font-weight:700;font-size:13px;display:flex;align-items:center;justify-content:center}

/* footer */
.footer{left:0;top:2063px;width:1200px;height:296px;background:var(--slate)}
.footer-brand{left:99px;top:2126px}
.footer-brand .brand{color:var(--white)}
.footer-about{left:99px;top:2171px;width:230px;font-size:12px;line-height:24px;color:#e6e6ee}
.pay-badge{top:2244px;width:36px;height:20px;background:var(--white);border-radius:2px}
.col-rule{top:2093px;width:1px;height:185px;background:#55536f}
.f-col{top:2100px;color:#e6e6ee;font-size:12px}
.f-col h4{font-family:'Raleway',sans-serif;font-weight:700;font-size:15px;color:var(--white);margin-bottom:14px}
.f-col li{list-style:none;line-height:22.5px}
.f-col.links li{text-decoration:underline}
.contact-row{display:flex;gap:14px;line-height:21px}
.contact-row svg{flex:none;margin-top:5px}
.copyright{left:99px;top:2314px;font-size:12px;color:var(--white)}
.follow{left:797px;top:2314px;font-size:12px;color:var(--white)}
.social{top:2309px;width:26px;height:26px;background:var(--white);border-radius:4px}
</style>
</head>
<body>

<div class="abs top-bar"></div>
<header>
  <div class="abs site-brand brand"><span class="brand-mark"></span>ourTradeLoop</div>
  <nav>
    <span class="abs nav-link" style="left:738px">How it works</span>
    <span class="abs nav-link" style="left:874px">Help</span>
    <span class="abs nav-btn buy">Buy</span>
    <span class="abs nav-btn sell">Sell</span>
  </nav>
</header>

<section class="abs hero">
  <svg width="1200" height="480" viewBox="0 0 1200 480">
    <polygon points="637,0 1200,0 1200,417 558,480" fill="var(--hero-grey)"/>
    <polygon points="0,0 637,0 558,478 0,417" fill="var(--red)"/>
    <g role="img" aria-label="Photo of a black smartphone">
      <rect x="283" y="28" width="197" height="405" rx="28" fill="#1f2a3a"/>
      <rect x="295" y="84" width="175" height="300" fill="#4a8fc8"/>
    </g>
    <g role="img" aria-label="Photo of a white smartphone">
      <rect x="716" y="22" width="290" height="440" rx="36" fill="#f7f7f7" stroke="#cfcfcf"/>
      <rect x="858" y="84" width="140" height="270" fill="#5d7fb0"/>
    </g>
  </svg>
  <div class="abs hero-label" style="left:598px;top:129px;width:283px;height:119px"><b>SELL</b><span>Cash Your Electonics</span></div>
  <div class="abs hero-label" style="left:313px;top:249px;width:285px;height:120px"><b>BUY</b><span>Certified Electonics</span></div>
</section>

<section>
  <h2 class="abs heading" style="top:632px">CLICK YOUR GADGET TO SELL</h2>
  <p class="abs lead" style="top:678px">Sed ut perspiciatis unde omnis iste natus error sit voluptatem accusantium doloremque laudantium, totam rem aperiam, eaque ipsa quae ab illo inventore veritatis et quasi architecto beatae vitae dicta sunt explicabo.</p>
  <svg class="abs arrow" style="left:100px" width="16" height="34" viewBox="0 0 16 34"><polyline points="14,2 2,17 14,32" fill="none" stroke="#bbb" stroke-width="2"/></svg>
  <svg class="abs arrow" style="left:1083px" width="16" height="34" viewBox="0 0 16 34"><polyline points="2,2 14,17 2,32" fill="none" stroke="#bbb" stroke-width="2"/></svg>
  <div class="abs gadget" style="left:178px;background:var(--green)"><svg width="50" height="44" viewBox="0 0 50 44" fill="none" stroke="#fff" stroke-width="4"><rect x="3" y="3" width="44" height="28" rx="2"/><line x1="25" y1="31" x2="25" y2="40"/><line x1="14" y1="41" x2="36" y2="41"/></svg></div>
  <div class="abs gadget" style="left:357px;background:var(--yellow)"><svg width="54" height="36" viewBox="0 0 54 36" fill="none" stroke="#fff" stroke-width="4"><rect x="9" y="3" width="36" height="24" rx="2"/><line x1="2" y1="32" x2="52" y2="32"/></svg></div>
  <div class="abs gadget" style="left:536px;background:var(--blue)"><svg width="36" height="46" viewBox="0 0 36 46" fill="none" stroke="#fff" stroke-width="4"><rect x="3" y="3" width="30" height="40" rx="4"/><circle cx="18" cy="37" r="1.5" fill="#fff"/></svg></div>
  <div class="abs gadget" style="left:717px;background:var(--red-soft)"><svg width="26" height="46" viewBox="0 0 26 46" fill="none" stroke="#fff" stroke-width="4"><rect x="3" y="3" width="20" height="40" rx="4"/><line x1="10" y1="36" x2="16" y2="36"/></svg></div>
  <div class="abs gadget" style="left:896px;background:var(--orange)"><svg width="60" height="34" viewBox="0 0 60 34"><rect x="2" y="2" width="56" height="30" rx="15" fill="#fff"/><rect x="13" y="14" width="14" height="5" fill="var(--orange)"/><rect x="17.5" y="9.5" width="5" height="14" fill="var(--orange)"/><circle cx="40" cy="13" r="3" fill="var(--orange)"/><circle cx="46" cy="20" r="3" fill="var(--orange)"/></svg></div>
</section>

<section>
  <div class="abs app-band" role="img" aria-label="Background photo of a person using a phone, tinted slate"></div>
  <h2 class="abs app-title">OURTRADELOOP MOBILE APP</h2>
  <p class="abs app-copy">Lorem ipsum dolor sit amet, consectetur adipiscing elit, sed do eiusmod tempor incididunt ut labore et dolore magna aliqua. Ut enim ad minim veniam, quis nostrud exercitation ullamco laboris nisi ut aliquip ex ea commodo consequat. Duis aute irure dolor in reprehenderit in voluptate velit esse cillum dolore</p>
  <div class="abs store-badge" style="left:168px" role="img" aria-label="App store download badge"></div>
  <div class="abs store-badge" style="left:330px" role="img" aria-label="App store download badge"></div>
  <div class="abs hand-photo" role="img" aria-label="Photo of a hand holding a phone showing the app install screen"></div>
</section>

<section>
  <h2 class="abs heading" style="top:1372px">HOW TO SELL YOUR PRODUCT</h2>
  <p class="abs lead" style="top:1422px">Sed ut perspiciatis unde omnis iste natus error sit voluptatem accusantium doloremque laudantium, totam rem aperiam, eaque ipsa quae ab illo inventore veritatis et quasi architecto beatae vitae dicta sunt explicabo.</p>
  <a class="abs cta">CLICK HERE TO READ MORE</a>
</section>

<section>
  <div class="abs why"></div>
  <h2 class="abs heading" style="top:1655px">WHY CUSTOMERS CHOOSE US</h2>
  <div class="abs feature" style="left:105px">
    <svg width="90" height="70" viewBox="0 0 90 70" fill="var(--red)"><circle cx="20" cy="18" r="15" fill="none" stroke="var(--red)" stroke-width="5"/><polyline points="20,10 20,19 27,19" fill="none" stroke="var(--red)" stroke-width="4"/><rect x="12" y="28" width="46" height="28"/><path d="M58 34h16l10 12v10H58z"/><circle cx="26" cy="60" r="7" stroke="var(--panel)" stroke-width="3"/><circle cx="72" cy="60" r="7" stroke="var(--panel)" stroke-width="3"/></svg>
    <h3>FAST DELIVERY</h3>
    <p>Our standard delivery service is FREE in UK, regardless of the size and value. We are committed to offering fast and free delivery.</p>
  </div>
  <div class="abs feature" style="left:454px">
    <svg width="90" height="70" viewBox="0 0 90 70" fill="var(--red)"><rect x="6" y="8" width="56" height="34" rx="4" transform="rotate(-14 34 25)"/><rect x="16" y="22" width="56" height="34" rx="4" stroke="var(--panel)" stroke-width="3"/><rect x="22" y="38" width="12" height="5" fill="var(--panel)"/><rect x="62" y="48" width="22" height="18" rx="2"/><path d="M66 48v-6a7 7 0 0 1 14 0v6" fill="none" stroke="var(--red)" stroke-width="3"/></svg>
    <h3>SAFE &amp; SECURE PAYMENT</h3>
    <p>Here at ourTradeLoop we like to ensure that our customers can purchase from us with confidence &amp; 100% safe and secure payment methods.</p>
  </div>
  <div class="abs feature" style="left:813px">
    <svg width="90" height="70" viewBox="0 0 90 70"><rect x="10" y="10" width="70" height="50" fill="var(--red)"/><rect x="17" y="17" width="56" height="36" fill="none" stroke="#fff" stroke-width="2"/><circle cx="45" cy="35" r="13" fill="#fff"/><text x="45" y="41" text-anchor="middle" font-family="Open Sans,sans-serif" font-weight="700" font-size="17" fill="var(--red)">1</text></svg>
    <h3>100% MONEY BACK GUARANTEED</h3>
    <p>To prove our confidence in the services we provide, we are offering a generous 60 day, money back, satisfaction guarantee!</p>
  </div>
</section>

<section>
  <div class="abs newsletter"></div>
  <svg class="abs" style="left:96px;top:2000px" width="46" height="40" viewBox="0 0 46 40"><g transform="rotate(-15 23 20)"><rect x="3" y="8" width="40" height="26" rx="2" fill="#fff"/><polyline points="3,9 23,24 43,9" fill="none" stroke="var(--red)" stroke-width="2.5"/></g></svg>
  <div class="abs nl-label"><small>NEWSLETTER</small><strong>SUBSCRIPTION</strong></div>
  <div class="abs nl-input">ENTER EMAIL ADDRESS</div>
  <div class="abs nl-btn">SUBSCRIBE</div>
</section>

<footer>
  <div class="abs footer"></div>
  <div class="abs footer-brand"><div class="brand"><span class="brand-mark"></span>ourTradeLoop</div></div>
  <p class="abs footer-about">At vero eos et accusamus et iusto odio dignissimos ducimus qui blan</p>
  <div class="abs pay-badge" style="left:99px"></div>
  <div class="abs pay-badge" style="left:139px"></div>
  <div class="abs pay-badge" style="left:179px"></div>
  <div class="abs pay-badge" style="left:219px;width:64px"></div>

  <div class="abs col-rule" style="left:340px"></div>
  <div class="abs col-rule" style="left:519px"></div>
  <div class="abs col-rule" style="left:688px"></div>
  <div class="abs col-rule" style="left:890px"></div>

  <div class="abs f-col links" style="left:376px"><h4>QUICK LINKS</h4><ul><li>Contact</li><li>FAQ</li><li>Delivery</li><li>Returns</li><li>Track Orders</li><li>Subscribe</li></ul></div>
  <div class="abs f-col" style="left:561px"><h4>EXTRAS</h4><ul><li>Specials</li><li>New products</li><li>Top sellers</li><li>Our stores</li><li>Contact us</li><li>About us</li></ul></div>
  <div class="abs f-col" style="left:725px"><h4>MY ACCOUNT</h4><ul><li>Delivery Information</li><li>Privacy Policy</li><li>Returns Policy</li><li>Terms and Conditions</li><li>FAQs</li></ul></div>
  <div class="abs f-col" style="left:940px"><h4>CONTACT US</h4>
    <div class="contact-row" style="margin-bottom:20px"><svg width="9" height="12" viewBox="0 0 9 12"><path d="M4.5 0A4.5 4.5 0 0 0 0 4.5C0 8 4.5 12 4.5 12S9 8 9 4.5A4.5 4.5 0 0 0 4.5 0z" fill="#fff"/><circle cx="4.5" cy="4.5" r="1.6" fill="var(--slate)"/></svg><span>27 Harrow Lane,<br>London EC2A 4RT</span></div>
    <div class="contact-row" style="margin-bottom:20px"><svg width="10" height="10" viewBox="0 0 10 10"><path d="M2 0l2 2.5-1 1.5a6 6 0 0 0 3 3l1.5-1L10 8l-1.5 2C4 10 0 6 0 1.5z" fill="#fff"/></svg><span>020 7946 0318</span></div>
    <div class="contact-row"><svg width="11" height="8" viewBox="0 0 11 8"><rect width="11" height="8" fill="#fff"/><polyline points="0,0 5.5,4.5 11,0" fill="none" stroke="var(--slate)"/></svg><span style="text-decoration:underline">hello@ourtradeloop.com</span></div>
  </div>

  <p class="abs copyright">Copyrights © 2016, ourTradeLoop.  All Rights Reserved</p>
  <p class="abs follow">Follow us on :</p>
  <div class="abs social" style="left:893px"></div>
  <div class="abs social" style="left:929px"></div>
  <div class="abs social" style="left:965px"></div>
  <div class="abs social" style="left:1001px"></div>
  <div class="abs social" style="left:1037px"></div>
  <div class="abs social" style="left:1073px"></div>
</footer>

</body>
</html>
```